Biz Card Design TVCP

New business card for a new company.
Logo was completed by a designer on ArtHarbor and looking to continue requesting additional services.
Company Name: Tidal Vector Power Consulting
Although this company is starting in Canada, we will be moving towards a global presence within the next 6 months.
Key elements to this business are as follows.
Energy Procurement
Energy Reduction Services
Demand Side Consulting
Energy Efficiency Consulting
Saving Clients Money
Helping Them Go "Green"
Managing Their Energy Requirements
Basically the goal for our company is to find the best procurement solution for our clients and reduce their energy consumption. This reduces their expenses and the amount of greenhouse gas they produce on a daily basis.
I have been in the energy footprint for the last 20 years and know that most companies are looking to "do whatever is necessary to get them to sign on the dotted line". I would prefer to walk away from a client that I can't help than to put them into a situation that they will regret for years to come. This is where the "TIDAL" part of the company name comes from.
The following is a catch phrase that encompasses what we do.
"Reducing your carbon footprint & energy bill at the same time!"
The back of the card needs to have this statement along with some sort of illustration. The back is a playground for creative ideas.
The front of the card needs the following.
Logo.
First & Last Name (Gus Marwick)
Title (Energy Warrior)
Phone Number (555) 314-2718
Fax Number (555) 271-8314
Email Address gus@tidalvectorpowerconsulting.example
Address 47 fenwick rd Toronto Ontario K4T 2P9
I want it to be a card that is remembered when any of my staff give it to a customer. It HAS to stand out.
Target Market(s)
Business Owners, Decision Makers, 30 to 65+
Industry/Entity Type
Business
Look and feel

```html
<!DOCTYPE html>
<html lang="en">
<head>
<meta charset="utf-8">
<title>Tidal Vector Power Consulting — Business Card</title>
<link href="https://fonts.googleapis.com/css2?family=Open+Sans:ital,wght@0,400;0,600;0,700;1,400&display=swap" rel="stylesheet">
<style>
  :root {
    --stage: #0d0d0d;
    --green: #22b04b;
    --green-deep: #1c9a40;
    --blue: #3f72bd;
    --blue-deep: #2f5aa3;
    --white: #ffffff;
    --ink-blue: #3a6bbb;
  }
  * { box-sizing: border-box; margin: 0; padding: 0; }
  html, body {
    width: 1200px; height: 900px; overflow: hidden;
    background: var(--stage);
    font-family: "Open Sans", Arial, sans-serif;
  }
  .stage {
    width: 1200px; height: 900px;
    display: flex; flex-direction: column;
    align-items: center; justify-content: center; gap: 40px;
  }
  .card {
    width: 680px; height: 389px;
    position: relative; overflow: hidden;
    box-shadow: 0 6px 18px rgba(0,0,0,.6);
  }

  /* Back of card */
  .card-back { background: var(--green); color: var(--white); }
  .card-back .company-name {
    position: absolute; left: 48px; top: 40px;
    font-weight: 700; font-size: 30px; letter-spacing: -0.3px;
  }
  .service-list {
    position: absolute; left: 52px; top: 98px;
    list-style: none;
  }
  .service-list li {
    display: flex; align-items: center; gap: 12px;
    font-size: 17px; line-height: 32px;
  }
  .service-list .bullet {
    width: 12px; height: 12px; border-radius: 50%;
    background: var(--white); flex: none;
  }
  .tagline-band {
    position: absolute; left: 0; right: 0; bottom: 0; height: 46px;
    background: var(--blue-deep);
    display: flex; align-items: center; justify-content: center;
    font-size: 16px; color: var(--white);
  }

  /* Front of card */
  .card-front { background: var(--white); }
  .front-logo {
    position: absolute; left: 0; right: 0; top: 0; height: 206px;
    display: flex; align-items: center; justify-content: center; gap: 14px;
  }
  .front-logo .mark-dot {
    width: 26px; height: 26px; border-radius: 50%; background: var(--green);
  }
  .front-logo .company-name {
    font-weight: 700; font-size: 34px; color: var(--ink-blue); letter-spacing: -0.4px;
  }
  .name-band {
    position: absolute; left: 0; right: 0; top: 206px; height: 46px;
    background: var(--blue);
    display: flex; align-items: center; padding-left: 44px;
    color: var(--white); font-size: 22px; font-weight: 600;
  }
  .name-band .divider { margin: 0 14px; font-weight: 400; }
  .name-band .job-title { font-size: 19px; font-weight: 600; }
  .contact-panel {
    position: absolute; left: 0; right: 0; top: 252px; bottom: 0;
    background: var(--green); color: var(--white);
    padding: 16px 44px 0;
  }
  .contact-columns { display: flex; gap: 48px; }
  .contact-col { list-style: none; }
  .contact-col li {
    display: flex; align-items: center; gap: 10px;
    font-size: 15px; line-height: 28px;
  }
  .contact-col svg { width: 16px; height: 16px; flex: none; }
  .contact-panel .tagline {
    margin-top: 16px; text-align: center; font-size: 16px;
  }
</style>
</head>
<body>
<main class="stage">

  <section class="card card-back" aria-label="Card back">
    <h2 class="company-name">Tidal Vector Power Consulting</h2>
    <ul class="service-list">
      <li><span class="bullet"></span>Energy Procurement</li>
      <li><span class="bullet"></span>Energy Reduction Services</li>
      <li><span class="bullet"></span>Demand Side Consulting</li>
      <li><span class="bullet"></span>Energy Efficiency Consulting</li>
      <li><span class="bullet"></span>Saving Clients Money</li>
      <li><span class="bullet"></span>Helping Them Go "Green"</li>
      <li><span class="bullet"></span>Managing Their Energy Requirements</li>
    </ul>
    <p class="tagline-band">"Reducing your carbon footprint &amp; energy bill at the same time!"</p>
  </section>

  <section class="card card-front" aria-label="Card front">
    <div class="front-logo">
      <span class="mark-dot"></span>
      <h1 class="company-name">Tidal Vector Power Consulting</h1>
    </div>
    <div class="name-band">
      <span class="person-name">Gus Marwick</span>
      <span class="divider">|</span>
      <span class="job-title">Energy Warrior</span>
    </div>
    <div class="contact-panel">
      <div class="contact-columns">
        <ul class="contact-col">
          <li>
            <svg viewBox="0 0 16 16" aria-label="Phone"><rect x="0.5" y="0.5" width="15" height="15" rx="3" fill="none" stroke="#fff"/><path d="M5 4c0 4 3 7 7 7l1-2-2-1-1 1c-1-.5-2-1.5-2.5-2.5l1-1-1-2z" fill="#fff"/></svg>
            (555) 314-2718
          </li>
          <li>
            <svg viewBox="0 0 16 16" aria-label="Fax"><rect x="0.5" y="0.5" width="15" height="15" rx="3" fill="none" stroke="#fff"/><rect x="4" y="6" width="8" height="6" fill="none" stroke="#fff"/><rect x="5.5" y="3.5" width="5" height="3" fill="#fff"/></svg>
            (555) 271-8314
          </li>
        </ul>
        <ul class="contact-col">
          <li>
            <svg viewBox="0 0 16 16" aria-label="Email"><rect x="0.5" y="0.5" width="15" height="15" rx="3" fill="none" stroke="#fff"/><rect x="3.5" y="5" width="9" height="6" fill="none" stroke="#fff"/><path d="M3.5 5l4.5 3.5L12.5 5" fill="none" stroke="#fff"/></svg>
            gus@tidalvectorpowerconsulting.example
          </li>
          <li>
            <svg viewBox="0 0 16 16" aria-label="Address"><rect x="0.5" y="0.5" width="15" height="15" rx="3" fill="none" stroke="#fff"/><path d="M3.5 8L8 4l4.5 4M5 7.5V12h6V7.5" fill="none" stroke="#fff"/></svg>
            47 fenwick rd Toronto Ontario K4T 2P9
          </li>
        </ul>
      </div>
      <p class="tagline">"Reducing your carbon footprint &amp; energy bill at the same time!"</p>
    </div>
  </section>

</main>
</body>
</html>
```